Marlowe Group needs a business card

I would like the card to be simple but modern and elegant.
I like black and white.
or black and gold.
we are a private finance lender and also are involved in property and property developments.

please look at the business card photos i provided i would like Marlowe Group only one one side and all the other details on the other side use fonts that tie in with my theme.

Industry/Entity Type

Finance

Contact Information for Business Card

Marlowe Group (Marlowe Group) Daniel Marlowe M: 0413586207 E: danmarl@inboxmail.test

Font styles to use
Other font styles liked:
• Use fonts that would reflect our business

Colors
000000
ffffff

Requirements
Must have
• one side of details
• other side has either Marlowe Group or Marlowe Group like in the photos provided

```html
<!DOCTYPE html>
<html lang="en">
<head>
<meta charset="utf-8">
<title>Marlowe Group — Business Card</title>
<link rel="stylesheet" href="https://fonts.googleapis.com/css2?family=Montserrat:wght@500;700&display=swap">
<style>
  :root {
    --backdrop: #7b7e80;
    --card: #f4f4f4;
    --ink: #000000;
    --card-shadow: rgba(0, 0, 0, 0.28);
  }
  * { margin: 0; padding: 0; box-sizing: border-box; }
  html, body {
    width: 1200px;
    height: 814px;
    overflow: hidden;
    background: var(--backdrop);
  }
  .canvas {
    position: relative;
    width: 1200px;
    height: 814px;
    display: flex;
    align-items: center;
    justify-content: center;
    gap: 70px;
  }
  .card {
    width: 500px;
    height: 306px;
    background: var(--card);
    box-shadow: 0 14px 30px var(--card-shadow);
    display: flex;
    align-items: center;
    justify-content: center;
    font-family: "Montserrat", sans-serif;
    color: var(--ink);
  }
  .card--details {
    flex-direction: column;
    text-align: center;
  }
  .card__name {
    font-weight: 700;
    font-size: 19px;
    letter-spacing: 0.2px;
    margin-bottom: 10px;
  }
  .card__line {
    font-weight: 500;
    font-size: 16px;
    line-height: 1.32;
    letter-spacing: 0.3px;
  }
  .card--brand {
    align-items: flex-start;
    padding-top: 88px;
  }
  .card__brand-name {
    font-weight: 700;
    font-size: 38px;
    letter-spacing: 0.5px;
  }
</style>
</head>
<body>
  <main class="canvas">
    <section class="card card--details" aria-label="Contact side">
      <p class="card__name">Daniel Marlowe</p>
      <p class="card__line">Cell : 0413586207</p>
      <p class="card__line">danmarl@inboxmail.test</p>
      <p class="card__line">www.marlowegroup.test</p>
    </section>
    <section class="card card--brand" aria-label="Company name side">
      <p class="card__brand-name">Marlowe Group</p>
    </section>
  </main>
</body>
</html>
```